Poster for a online company that buys your stuff

SwapKestrel offers a website which customers can get a instant offer for stuff their looking to sell. They then Courier the items in to us and they get paid the same day it arrives
We're looking for an eye catching design which portrays our hassle free process
We'll need your help to come up with a slogan/catch phrase and our easy 1,2,3 process so customers can see the poster and instantly have a clear understanding of what we do
1. Get an instant offer on our website
2. Send your item(s) to us
3.Get paid within 24 Hours
Industry/Entity Type
It Company
Look and feel
Each slider illustrates characteristics of the customer's brand and the style your logo design should communicate.

```html
<!DOCTYPE html>
<html lang="en">
<head>
<meta charset="utf-8">
<title>SwapKestrel Poster</title>
<link href="https://fonts.googleapis.com/css2?family=Arimo:wght@400;700&display=swap" rel="stylesheet">
<style>
  :root {
    --backdrop: #6b6b6b;
    --paper: #ffffff;
    --green: #0d8a1f;
    --green-deep: #0b7a1a;
    --green-light: #7cc21f;
    --green-ring: #8cc63f;
    --ink: #2b2b2b;
    --text-green: #1c6b1c;
  }
  * { margin: 0; padding: 0; box-sizing: border-box; }
  html, body { width: 900px; height: 1200px; overflow: hidden; background: var(--backdrop); }
  body { font-family: "Arimo", Arial, sans-serif; position: relative; }

  .poster {
    position: absolute; left: 148px; top: 150px; width: 632px; height: 892px;
    background: var(--paper); overflow: hidden;
  }
  .hero-band { position: absolute; inset: 0; width: 632px; height: 892px; }

  .mascot-art {
    position: absolute; left: 152px; top: 25px; width: 390px; height: 330px;
    border-radius: 40% 45% 30% 35%;
    background: radial-gradient(ellipse at 45% 45%, #f3a21b 0%, #8ccc2a 45%, rgba(124,194,31,0) 72%);
    opacity: .85;
  }

  .brand-name {
    position: absolute; left: 0; width: 632px; top: 352px; text-align: center;
    font-weight: 700; font-size: 58px; letter-spacing: -1.5px; color: var(--ink);
  }
  .headline-top {
    position: absolute; left: 0; width: 632px; top: 432px; text-align: center;
    font-weight: 700; font-size: 33px; color: var(--ink); letter-spacing: .5px;
  }
  .headline-main {
    position: absolute; left: 0; width: 632px; top: 472px; text-align: center;
    font-weight: 400; font-size: 96px; color: var(--green); letter-spacing: 10px; line-height: 1;
  }
  .headline-sub {
    position: absolute; left: 0; width: 632px; top: 570px; text-align: center;
    font-weight: 700; font-size: 36px; color: var(--green);
  }
  .headline-rule { position: absolute; left: 112px; top: 614px; width: 406px; height: 16px; }

  .steps { position: absolute; left: 0; top: 650px; width: 632px; height: 160px; }
  .step { position: absolute; top: 0; width: 200px; text-align: center; }
  .step-number {
    position: absolute; top: 0; font-size: 24px; color: var(--text-green); left: 38px;
  }
  .step-badge { display: block; margin: 0 auto; width: 112px; height: 112px; }
  .step-caption { margin-top: 6px; font-size: 15px; line-height: 20px; color: var(--text-green); }
  .step-divider { position: absolute; top: 8px; width: 1px; height: 142px; background: #8a8a8a; }

  .contact-bar { position: absolute; left: 0; top: 834px; width: 632px; height: 58px; }
  .contact-label {
    position: absolute; left: 38px; top: 838px; font-size: 38px; color: #fff; font-weight: 400;
  }
  .contact-number {
    position: absolute; left: 290px; top: 840px; font-size: 34px; font-weight: 700;
    color: var(--green-deep); letter-spacing: .5px;
  }
</style>
</head>
<body>
  <main class="poster">
    <svg class="hero-band" viewBox="0 0 632 892" aria-hidden="true">
      <defs>
        <linearGradient id="heroGreen" x1="0" y1="0" x2="1" y2="0.4">
          <stop offset="0" stop-color="#1fa33a"/>
          <stop offset="0.5" stop-color="#6bb823"/>
          <stop offset="1" stop-color="#2aa236"/>
        </linearGradient>
      </defs>
      <polygon points="0,0 632,0 0,470" fill="url(#heroGreen)"/>
    </svg>

    <div class="mascot-art" role="img" aria-label="Cartoon courier in a green cap giving a thumbs up while running with an orange parcel"></div>

    <div class="brand-name">SwapKestrel</div>
    <div class="headline-top">SELL YOUR PRODUCTS</div>
    <div class="headline-main">EASILY</div>
    <div class="headline-sub">IN 3 SIMPLE STEPS</div>
    <svg class="headline-rule" viewBox="0 0 406 16" aria-hidden="true">
      <polyline points="0,6 188,6 203,14 218,6 406,6" fill="none" stroke="#0d8a1f" stroke-width="1.5"/>
    </svg>

    <section class="steps">
      <div class="step" style="left:13px">
        <span class="step-number" style="left:35px">1</span>
        <svg class="step-badge" viewBox="0 0 112 112" aria-hidden="true">
          <circle cx="56" cy="56" r="55" fill="#8cc63f"/>
          <circle cx="56" cy="56" r="46" fill="#0d8a1f"/>
          <g fill="none" stroke="#fff" stroke-width="2">
            <circle cx="56" cy="56" r="26"/>
            <ellipse cx="56" cy="56" rx="11" ry="26"/>
            <line x1="56" y1="30" x2="56" y2="82"/>
            <line x1="30" y1="56" x2="82" y2="56"/>
            <line x1="34" y1="43" x2="78" y2="43"/>
            <line x1="34" y1="69" x2="78" y2="69"/>
          </g>
        </svg>
        <p class="step-caption">Get an instant<br>offer on our website</p>
      </div>
      <div class="step-divider" style="left:217px"></div>
      <div class="step" style="left:224px">
        <span class="step-number" style="left:32px">2</span>
        <svg class="step-badge" viewBox="0 0 112 112" aria-hidden="true">
          <circle cx="56" cy="56" r="55" fill="#8cc63f"/>
          <circle cx="56" cy="56" r="46" fill="#0d8a1f"/>
          <g fill="none" stroke="#fff" stroke-width="2">
            <path d="M32 34 h6 v38 h40"/>
            <rect x="46" y="44" width="28" height="24"/>
            <line x1="53" y1="44" x2="53" y2="68"/>
            <line x1="60" y1="44" x2="60" y2="68"/>
            <line x1="67" y1="44" x2="67" y2="68"/>
            <circle cx="44" cy="78" r="4"/>
            <circle cx="72" cy="78" r="4"/>
          </g>
        </svg>
        <p class="step-caption">Send your<br>item(s) to us</p>
      </div>
      <div class="step-divider" style="left:424px"></div>
      <div class="step" style="left:435px">
        <span class="step-number" style="left:30px">3</span>
        <svg class="step-badge" viewBox="0 0 112 112" aria-hidden="true">
          <circle cx="56" cy="56" r="55" fill="#8cc63f"/>
          <circle cx="56" cy="56" r="46" fill="#0d8a1f"/>
          <path d="M36 46 A24 24 0 1 1 40 72" fill="none" stroke="#fff" stroke-width="3"/>
          <polygon points="30,44 42,44 36,54" fill="#fff"/>
          <text x="60" y="52" fill="#fff" font-family="Arimo, sans-serif" font-size="15" text-anchor="middle">P</text>
          <text x="50" y="73" fill="#fff" font-family="Arimo, sans-serif" font-weight="700" font-size="17" text-anchor="middle">24h</text>
        </svg>
        <p class="step-caption">Get paid<br>within 24 Hours</p>
      </div>
    </section>

    <svg class="contact-bar" viewBox="0 0 632 58" aria-hidden="true">
      <polygon points="0,0 198,0 238,50 632,50 632,58 0,58" fill="#0b7a1a"/>
      <circle cx="264" cy="25" r="16" fill="none" stroke="#0b7a1a" stroke-width="2"/>
      <path d="M257 17 q-3 3 0 9 q4 7 10 9 q3 1 5 -2 l-4 -4 l-3 2 q-4 -2 -6 -7 l2 -3 z" fill="#0b7a1a"/>
    </svg>
    <div class="contact-label">Call us:</div>
    <div class="contact-number">077- 4812- 6039</div>
  </main>
</body>
</html>
```